Celebration Cake brochure for boutique cake store

Looking for a cake brochure which displays the photo of the cake along with the description. Don't mind what style of brochure or size you do. We are a boutique bakery with both Italian and Australian cakes. I have a few ranges of products that I need to produce brochures (such as other sweets) but this is the first one required. *more photo to come

Industry/Entity Type

Bakery

Font styles to use
Sans Serif

Colors

Designer to choose colors to be used in the design.

Requirements
Must have
• Easy for customers to use the brochure to choose their cake. Don't mind what size brochure/menu you use

```html
<!DOCTYPE html>
<html lang="en">
<head>
<meta charset="utf-8">
<title>Ferrante's Pasticceria – Celebration Cakes</title>
<link href="https://fonts.googleapis.com/css2?family=Marcellus&family=Hind:wght@400&display=swap" rel="stylesheet">
<style>
  :root{
    --paper:#e3d6a7;
    --paper-light:#ece2bb;
    --wine:#981f36;
    --cream:#f6eed6;
    --photo-dark:#3a2214;
    --photo-mid:#7a4a28;
    --photo-warm:#a86d3a;
  }
  *{box-sizing:border-box;margin:0;padding:0}
  html,body{width:1200px;height:960px;overflow:hidden}
  body{
    position:relative;
    background:radial-gradient(ellipse at 62% 40%, var(--paper-light) 0%, var(--paper) 70%);
    font-family:"Hind",sans-serif;
    color:var(--wine);
  }
  .top-band{
    position:absolute;left:0;top:70px;width:1200px;height:36px;
    background:var(--wine);
    display:flex;justify-content:flex-end;align-items:center;
    padding-right:42px;gap:22px;
    color:var(--cream);font-size:18px;
  }
  .brand{
    position:absolute;left:24px;top:30px;
    display:flex;align-items:center;gap:8px;
  }
  .brand-square{width:16px;height:16px;background:var(--wine)}
  .brand-name{font-family:"Hind",sans-serif;font-weight:400;font-size:20px;color:var(--wine);line-height:1}
  .cake{position:absolute;display:flex;gap:6px}
  .cake-photo{
    flex:none;width:140px;height:130px;
    background:radial-gradient(ellipse at 50% 55%, var(--photo-warm) 0%, var(--photo-mid) 40%, var(--photo-dark) 100%);
  }
  .cake-info{padding-top:8px}
  .cake-name{font-family:"Marcellus",serif;font-weight:400;font-size:20.5px;line-height:1.05;margin-bottom:6px}
  .cake-desc{font-size:14px;line-height:1.32}
  .cake-desc.small{font-size:12.4px;line-height:1.3}
  .col-1 .cake-info{width:208px}
  .col-2 .cake-info{width:242px}
  .col-3 .cake-info{width:236px}
  .col-1{left:17px}.col-2{left:385px}.col-3{left:780px}
  .bottom-band{
    position:absolute;left:0;top:902px;width:1200px;height:36px;
    background:var(--wine);color:var(--cream);
    display:flex;justify-content:center;align-items:center;font-size:14.5px;
  }
</style>
</head>
<body>
  <div class="brand">
    <div class="brand-square"></div>
    <span class="brand-name">Ferrante's Pasticceria</span>
  </div>
  <div class="top-band">
    <span>Order Cakes Online: www.ferrantes.com.au</span>
    <span>Phone: 07 3412 8850</span>
  </div>

  <div class="cake col-1" style="top:173px">
    <div class="cake-photo" role="img" aria-label="Photo of apple crumble cake"></div>
    <div class="cake-info"><h2 class="cake-name">Apple Crumble</h2><p class="cake-desc">Shortbread flan with diced baked apples, cinnamon &amp; a layer of vanilla sponge encased in a crumble topping.</p></div>
  </div>
  <div class="cake col-1" style="top:318px">
    <div class="cake-photo" role="img" aria-label="Photo of apple pie"></div>
    <div class="cake-info" style="padding-top:18px"><h2 class="cake-name">Apple Pie</h2><p class="cake-desc">Baked apple in a tradition short-crust casing.</p></div>
  </div>
  <div class="cake col-1" style="top:459px">
    <div class="cake-photo" role="img" aria-label="Photo of Bianco Nero profiterole mound"></div>
    <div class="cake-info" style="padding-top:4px"><h2 class="cake-name">Bianco Nero</h2><p class="cake-desc small">Italian profiterole mound filled with chantilly cream, smothered in chocolate gianduia cream &amp; decorated with chocolate flakes &amp; strawberries. (Minimum 25 pieces - $3 per profiterole).</p></div>
  </div>
  <div class="cake col-1" style="top:606px">
    <div class="cake-photo" role="img" aria-label="Photo of Black Forest cake with cherries"></div>
    <div class="cake-info" style="padding-top:6px"><h2 class="cake-name">Black Forest</h2><p class="cake-desc small">Chocolate sponge soaked with herbal liqueur, layers of fresh cream, kirsch sour cherries &amp; finished with fresh cream, chocolate shavings &amp; maraschino cherries.</p></div>
  </div>
  <div class="cake col-1" style="top:750px">
    <div class="cake-photo" style="height:134px" role="img" aria-label="Photo of Cassata Siciliana cake"></div>
    <div class="cake-info" style="padding-top:10px"><h2 class="cake-name">Cassatta Sicilian</h2><p class="cake-desc small">Vanilla sponge with herbal liqueur, layers of sweet ricotta, glace orange &amp; chocolate bits. Topped with white fondant &amp; glace fruit then wrapped in green marzipan icing.</p></div>
  </div>

  <div class="cake col-2" style="top:173px">
    <div class="cake-photo" role="img" aria-label="Photo of chocolate hazelnut almond mud cake"></div>
    <div class="cake-info" style="padding-top:4px"><h2 class="cake-name">Chocolate Hazelnut Almond Mud</h2><p class="cake-desc">Nutty gluten-free cake made with chocolate &amp; almond meal &amp; finished with hazelnut decorations. Gluten free.</p></div>
  </div>
  <div class="cake col-2" style="top:318px">
    <div class="cake-photo" role="img" aria-label="Photo of chocolate mud cake"></div>
    <div class="cake-info" style="padding-top:10px"><h2 class="cake-name">Chocolate Mud</h2><p class="cake-desc">Thick melted chocolate sponge with a layer of ganache on top then decorated with chocolate.</p></div>
  </div>
  <div class="cake col-2" style="top:459px">
    <div class="cake-photo" role="img" aria-label="Photo of gluten free chocolate mud cake"></div>
    <div class="cake-info" style="padding-top:6px"><h2 class="cake-name">Gluten Free Chocolate Mud</h2><p class="cake-desc">Thick melted chocolate with gluten free sponge and a layer of ganache on top then decorated with chocolate.</p></div>
  </div>
  <div class="cake col-2" style="top:605px">
    <div class="cake-photo" role="img" aria-label="Photo of croquembouche tower"></div>
    <div class="cake-info" style="padding-top:6px"><h2 class="cake-name">Croquembousche</h2><p class="cake-desc">Profiteroles filled with vanilla &amp; or chocolate crema &amp; topped with toffee – to be served within 2 hours of picking up. (Minimum 25 pieces - $3 per profiterole).</p></div>
  </div>
  <div class="cake col-2" style="top:750px">
    <div class="cake-photo" style="height:134px" role="img" aria-label="Photo of chocolate hazelnut crostata tart"></div>
    <div class="cake-info" style="padding-top:10px"><h2 class="cake-name">Crostata Di Cioccolato</h2><p class="cake-desc">Shortbread tart filled with creamy ganache &amp; liqueur soaked vanilla sponge surrounded by diced almonds.</p></div>
  </div>

  <div class="cake col-3" style="top:170px">
    <div class="cake-photo" role="img" aria-label="Photo of Diplomatica cake"></div>
    <div class="cake-info" style="padding-top:8px"><h2 class="cake-name">Diplomatica</h2><p class="cake-desc">Vanilla sponge with herbal liqueur sandwiched between layers of vanilla custard &amp; puff pastry. Decorated with flakes of pastry &amp; fresh cream, &amp; then dusted with cocoa.</p></div>
  </div>
  <div class="cake col-3" style="top:315px">
    <div class="cake-photo" role="img" aria-label="Photo of Millefoglie cake with strawberries"></div>
    <div class="cake-info" style="padding-top:10px"><h2 class="cake-name">Millie Foglie</h2><p class="cake-desc">Traditional puff pastry vanilla slice made with Italian vanilla custard then topped with pastry flakes &amp; almonds.</p></div>
  </div>
  <div class="cake col-3" style="top:459px">
    <div class="cake-photo" role="img" aria-label="Photo of Monte Blanco white chocolate cake"></div>
    <div class="cake-info" style="padding-top:10px"><h2 class="cake-name">Monte Blanco</h2><p class="cake-desc">Orange liqueur chantilly cream with vanilla sponge surrounded with sponge crumb &amp; topped with a mound of white chocolate.</p></div>
  </div>
  <div class="cake col-3" style="top:605px">
    <div class="cake-photo" role="img" aria-label="Photo of Monte Nero chocolate cake"></div>
    <div class="cake-info" style="padding-top:8px"><h2 class="cake-name">Monte Nero</h2><p class="cake-desc">Orange liqueur chocolate chantilly cream with vanilla sponge surrounded with sponge crumb &amp; topped with a mound of chocolate.</p></div>
  </div>
  <div class="cake col-3" style="top:750px">
    <div class="cake-photo" style="height:133px" role="img" aria-label="Photo of Nocciola hazelnut cake"></div>
    <div class="cake-info" style="padding-top:8px"><h2 class="cake-name">Nocciola</h2><p class="cake-desc">Hazelnut flavoured cream with vanilla &amp; herbal liqueur covered in almonds &amp; strawberries.</p></div>
  </div>

  <div class="bottom-band">*Although all care is taken with gluten free/nut free products, they are baked in a kitchen which contains flour &amp; nuts.</div>
</body>
</html>
```